IT Product Event Invitations

We are requesting the design of two invitations for a series of technological events that will be held between the company Tidewell Labs and its partner in the Dominican Republic, Corvantel.
Both events represent the launch of the Tidewell Labs brand in the Dominican Republic.
The first event is an elegant dinner aimed at the banking sector of the Dominican Republic to showcase the "Ledgerline Banking Suite" software.
Event information:
- Descriptive text for the invitation: Corvantel y Tidewell Labs le invitan a descubrir cómo reducir costos, aumentar la automatización y mejorar la satisfacción de los clientes a través de una solución única para enfrentar los desafíos de la banca.
- Date: 25 de Septiembre
- Time: 7PM
- Location: El Pimiento, Av. Julián Marcano 318
In the invitation, consider using the colors of the Tidewell Labs and Corvantel brands if possible. You can find the logos in the webpage
The second event is a wine tasting to present "Harborview Operations Hub" aimed at various industries.
Event information:
- Descriptive text for the invitation: Corvantel y Tidewell Labs le invitan a conocer una solución que le permitirá a toda su empresa brindar una experiencia de servicio a otro nivel.
- Date: 26 de Septiembre
- Time: 7PM
In the invitation, consider using the colors of the Tidewell Labs and Corvantel brands if possible. You can find the logos in the web page.
Both invitations must have a button for participant registration and that when you click on the image, it will direct you to a form.
Form for Ledgerline Banking Suite: https://signup.corvantel-events.example/ledgerline-dinner
Form for Harborview Operations Hub: https://signup.corvantel-events.example/harborview-tasting
Target Market(s)
Enterprise Customers
Industry/Entity Type
Technology
Look and feel
Each slider illustrates characteristics of the customer's brand and the style your logo design should communicate.

```html
<!DOCTYPE html>
<html lang="es">
<head>
<meta charset="utf-8">
<title>Invitaciones – Tidewell Labs y Corvantel</title>
<link rel="stylesheet" href="https://fonts.googleapis.com/css2?family=Lexend:wght@400;500;600;700&family=Questrial&display=swap">
<style>
  :root {
    --page: #ecebea;
    --cream: #f7f2ec;
    --tan: #c7a98c;
    --button: #d4b8a0;
    --button-ring: #c6a587;
    --ink: #2f2f2f;
    --rule: #3a3a3a;
    --wine: #b01e5a;
    --wine-deep: #7e1238;
    --pin: #c9252c;
    --icon-green: #8fd18a;
  }
  html, body {
    margin: 0;
    width: 1200px;
    height: 762px;
    overflow: hidden;
    background: var(--page);
  }
  .invitation {
    position: absolute;
    left: 0;
    top: 63px;
    width: 1200px;
    height: 635px;
    background: var(--cream);
    overflow: hidden;
    font-family: "Questrial", sans-serif;
    color: var(--ink);
  }
  /* Dinner invitation opens at #cena; the wine tasting shows by default */
  .invitation--dinner { display: none; }
  #cena:target { display: block; }
  #cena:target ~ .invitation--tasting { display: none; }

  .backdrop { position: absolute; inset: 0; }
  .brand {
    position: absolute;
    top: 89px;
    transform: translateY(-50%);
    display: flex;
    align-items: center;
    gap: 8px;
    font-family: "Lexend", sans-serif;
    font-weight: 600;
    color: #111;
    white-space: nowrap;
  }
  .brand--host { right: 836px; font-size: 34px; letter-spacing: -0.5px; }
  .brand--partner { left: 427px; font-size: 27px; }
  .brand-dot { width: 30px; height: 30px; border-radius: 50%; background: var(--pin); }
  .brand-divider {
    position: absolute;
    left: 393px;
    top: 56px;
    width: 2px;
    height: 70px;
    background: var(--rule);
  }
  .title {
    position: absolute;
    left: 370px;
    top: 211px;
    transform: translate(-50%, -50%);
    margin: 0;
    font-family: "Lexend", sans-serif;
    font-weight: 500;
    font-size: 54px;
    letter-spacing: 0.5px;
    white-space: nowrap;
  }
  .lead {
    position: absolute;
    left: 370px;
    top: 243px;
    transform: translateX(-50%);
    width: 640px;
    margin: 0;
    text-align: center;
    font-size: 20px;
    line-height: 24.5px;
  }
  .schedule {
    position: absolute;
    left: 248px;
    top: 404px;
    width: 244px;
    height: 97px;
  }
  .schedule-frame { position: absolute; inset: 0; }
  .schedule-icon { position: absolute; left: 98px; top: -23px; }
  .schedule-date {
    position: absolute;
    left: 19px;
    right: 20px;
    top: 26px;
    padding-bottom: 3px;
    border-bottom: 1.5px solid var(--rule);
    text-align: center;
    font-family: "Lexend", sans-serif;
    font-weight: 600;
    font-size: 22px;
  }
  .schedule-time {
    position: absolute;
    left: 0;
    right: 0;
    top: 66px;
    text-align: center;
    font-family: "Lexend", sans-serif;
    font-weight: 600;
    font-size: 22px;
  }
  .venue {
    position: absolute;
    left: 140px;
    top: 570px;
    transform: translateY(-50%);
    display: flex;
    align-items: center;
    gap: 17px;
    font-size: 22.5px;
    white-space: nowrap;
  }
  .artwork {
    position: absolute;
    left: 780px;
    top: 67px;
    width: 256px;
    height: 424px;
    border-radius: 48% 48% 20px 20px / 32% 32% 20px 20px;
    background: radial-gradient(ellipse at 50% 35%, var(--wine) 0%, var(--wine-deep) 55%, rgba(176, 30, 90, 0.15) 100%);
    opacity: 0.85;
  }
  .register {
    position: absolute;
    left: 668px;
    top: 495px;
    width: 474px;
    height: 95px;
    box-sizing: border-box;
    border: 2px solid var(--button-ring);
    border-radius: 48px;
    padding: 5px;
    text-decoration: none;
    background: var(--cream);
  }
  .register-face {
    display: flex;
    flex-direction: column;
    align-items: center;
    justify-content: center;
    height: 100%;
    border-radius: 42px;
    border: 2px solid var(--button-ring);
    box-sizing: border-box;
    background: var(--button);
    color: #fff;
    font-family: "Lexend", sans-serif;
  }
  .register-main { font-weight: 600; font-size: 40px; line-height: 40px; letter-spacing: 0.5px; }
  .register-sub { font-weight: 400; font-size: 16px; letter-spacing: 5px; margin-top: 2px; }
</style>
</head>
<body>
  <!-- Ledgerline Banking Suite dinner -->
  <main class="invitation invitation--dinner" id="cena">
    <svg class="backdrop" width="1200" height="635" viewBox="0 0 1200 635" aria-hidden="true">
      <polygon points="0,0 91,0 430,635 0,635" fill="var(--tan)"/>
      <polygon points="1039,0 1200,0 1200,239" fill="var(--tan)"/>
    </svg>
    <div class="brand brand--host">Tidewell Labs</div>
    <div class="brand-divider"></div>
    <div class="brand brand--partner"><span class="brand-dot"></span>Corvantel</div>
    <h1 class="title">Invitación</h1>
    <p class="lead">Corvantel y Tidewell Labs le invitan a descubrir cómo reducir costos,<br>aumentar la automatización y mejorar la satisfacción de los<br>clientes a través de una solución única para enfrentar<br>los desafíos de la banca.</p>
    <section class="schedule">
      <svg class="schedule-frame" width="244" height="97" viewBox="0 0 244 97" aria-hidden="true">
        <polyline points="1,97 1,1 90,1" fill="none" stroke="var(--rule)" stroke-width="1.2"/>
        <polyline points="154,1 243,1 243,97" fill="none" stroke="var(--rule)" stroke-width="1.2"/>
      </svg>
      <svg class="schedule-icon" width="48" height="46" viewBox="0 0 48 46" aria-hidden="true">
        <rect x="2" y="5" width="44" height="34" rx="4" fill="#fff" stroke="#222" stroke-width="2.5"/>
        <rect x="3" y="6" width="42" height="7" fill="var(--pin)"/>
        <line x1="11" y1="1" x2="11" y2="8" stroke="#222" stroke-width="2.5"/>
        <line x1="24" y1="1" x2="24" y2="8" stroke="#222" stroke-width="2.5"/>
        <line x1="37" y1="1" x2="37" y2="8" stroke="#222" stroke-width="2.5"/>
        <line x1="8" y1="21" x2="16" y2="21" stroke="#222" stroke-width="2.5"/>
        <line x1="8" y1="27" x2="14" y2="27" stroke="#222" stroke-width="2.5"/>
        <line x1="8" y1="33" x2="16" y2="33" stroke="#222" stroke-width="2.5"/>
        <circle cx="33" cy="31" r="12" fill="var(--icon-green)" stroke="#222" stroke-width="2.5"/>
        <polyline points="33,24 33,31 38,34" fill="none" stroke="#222" stroke-width="2.5"/>
      </svg>
      <div class="schedule-date">25 de Septiembre</div>
      <div class="schedule-time">7:00PM</div>
    </section>
    <div class="venue">
      <svg width="30" height="34" viewBox="0 0 30 34" aria-hidden="true">
        <path d="M15 2C9 2 5 6.5 5 12c0 7 10 16 10 16s10-9 10-16C25 6.5 21 2 15 2z" fill="none" stroke="var(--pin)" stroke-width="2"/>
        <circle cx="15" cy="12" r="4" fill="none" stroke="var(--pin)" stroke-width="2"/>
        <ellipse cx="15" cy="29" rx="12" ry="3.5" fill="none" stroke="var(--pin)" stroke-width="1.8"/>
      </svg>
      <span>El Pimiento, Av. Julián Marcano 318</span>
    </div>
    <div class="artwork" role="img" aria-label="Copa de vino tinto pintada en acuarela"></div>
    <a class="register" href="https://signup.corvantel-events.example/ledgerline-dinner">
      <span class="register-face">
        <span class="register-main">CLICK HERE</span>
        <span class="register-sub">TO REGISTER</span>
      </span>
    </a>
  </main>

  <!-- Harborview Operations Hub wine tasting -->
  <main class="invitation invitation--tasting" id="cata">
    <svg class="backdrop" width="1200" height="635" viewBox="0 0 1200 635" aria-hidden="true">
      <polygon points="0,0 91,0 430,635 0,635" fill="var(--tan)"/>
      <polygon points="1039,0 1200,0 1200,239" fill="var(--tan)"/>
    </svg>
    <div class="brand brand--host">Tidewell Labs</div>
    <div class="brand-divider"></div>
    <div class="brand brand--partner"><span class="brand-dot"></span>Corvantel</div>
    <h1 class="title">Invitación</h1>
    <p class="lead">Corvantel y Tidewell Labs le invitan a conocer una solución que le<br>permitirá a toda su empresa brindar una experiencia<br>de servicio a otro nivel.</p>
    <section class="schedule">
      <svg class="schedule-frame" width="244" height="97" viewBox="0 0 244 97" aria-hidden="true">
        <polyline points="1,97 1,1 90,1" fill="none" stroke="var(--rule)" stroke-width="1.2"/>
        <polyline points="154,1 243,1 243,97" fill="none" stroke="var(--rule)" stroke-width="1.2"/>
      </svg>
      <svg class="schedule-icon" width="48" height="46" viewBox="0 0 48 46" aria-hidden="true">
        <rect x="2" y="5" width="44" height="34" rx="4" fill="#fff" stroke="#222" stroke-width="2.5"/>
        <rect x="3" y="6" width="42" height="7" fill="var(--pin)"/>
        <line x1="11" y1="1" x2="11" y2="8" stroke="#222" stroke-width="2.5"/>
        <line x1="24" y1="1" x2="24" y2="8" stroke="#222" stroke-width="2.5"/>
        <line x1="37" y1="1" x2="37" y2="8" stroke="#222" stroke-width="2.5"/>
        <line x1="8" y1="21" x2="16" y2="21" stroke="#222" stroke-width="2.5"/>
        <line x1="8" y1="27" x2="14" y2="27" stroke="#222" stroke-width="2.5"/>
        <line x1="8" y1="33" x2="16" y2="33" stroke="#222" stroke-width="2.5"/>
        <circle cx="33" cy="31" r="12" fill="var(--icon-green)" stroke="#222" stroke-width="2.5"/>
        <polyline points="33,24 33,31 38,34" fill="none" stroke="#222" stroke-width="2.5"/>
      </svg>
      <div class="schedule-date">26 de Septiembre</div>
      <div class="schedule-time">7:00PM</div>
    </section>
    <div class="venue">
      <svg width="30" height="34" viewBox="0 0 30 34" aria-hidden="true">
        <path d="M15 2C9 2 5 6.5 5 12c0 7 10 16 10 16s10-9 10-16C25 6.5 21 2 15 2z" fill="none" stroke="var(--pin)" stroke-width="2"/>
        <circle cx="15" cy="12" r="4" fill="none" stroke="var(--pin)" stroke-width="2"/>
        <ellipse cx="15" cy="29" rx="12" ry="3.5" fill="none" stroke="var(--pin)" stroke-width="1.8"/>
      </svg>
      <span>El Pimiento, Av. Julián Marcano 318</span>
    </div>
    <div class="artwork" role="img" aria-label="Copa de vino tinto pintada en acuarela"></div>
    <a class="register" href="https://signup.corvantel-events.example/harborview-tasting">
      <span class="register-face">
        <span class="register-main">CLICK HERE</span>
        <span class="register-sub">TO REGISTER</span>
      </span>
    </a>
  </main>
</body>
</html>
```